Business cards for a fun web development agency

Hi,I am building a web development agency. You can read about it on the website http://kite-loft.examplehost.com. Basically, I want to focus on free and open source products and stay as far away from the corporate business feeling as possible. I want to build a community so I want the business card to feel fun and approachable (at the risk of professional if need be). I am uploading some of my image assets in various file formats. Feel free to use them or make your own if you want just keeping in theme with the website.
Industry/Entity Type
Building
Contact Information for Business Card
Company Name: Boat ShedWebsite: www.kiteloftdev.example (it's currently in alpha on http://kite-loft.examplehost.com if you want to see the them we are trying to capture)My name is: Banner B. SchaferMy email: banner@boatsheddev.comMy phone: 0431 587 904
Look and feel

```html
<!DOCTYPE html>
<html lang="en">
<head>
<meta charset="utf-8">
<title>Kite Loft — Business Card</title>
<link rel="stylesheet" href="https://fonts.googleapis.com/css2?family=Arimo:wght@400;500&display=swap">
<style>
  :root {
    --page-bg: #d9d4cc;
    --band-blue: #1f6b92;
    --band-blue-deep: #175a7e;
    --frost: #e9f1f5;
    --frost-edge: #d6e4ec;
    --ink-navy: #1f3650;
    --logo-blue: #2a6f98;
    --name-light: #e9eaeb;
    --services-light: #d2e3ec;
  }
  * { margin: 0; padding: 0; box-sizing: border-box; }
  html, body {
    width: 1200px; height: 970px; overflow: hidden;
    background: var(--page-bg);
    font-family: "Arimo", Arial, sans-serif;
  }
  .business-card {
    position: absolute; left: 100px; top: 207px;
    width: 1000px; height: 556px;
    background: linear-gradient(180deg, var(--frost) 0%, #f4f8fa 50%, var(--frost-edge) 100%);
    box-shadow: 0 14px 40px rgba(0,0,0,0.18);
    overflow: hidden;
  }
  .name-band {
    position: absolute; left: 0; top: 0; width: 100%; height: 107px;
    background: linear-gradient(90deg, var(--band-blue-deep), var(--band-blue) 60%, var(--band-blue-deep));
  }
  .holder-name {
    position: absolute; left: 36px; top: 28px;
    font-size: 56px; font-weight: 500; color: var(--name-light);
    letter-spacing: 0.5px; line-height: 1;
  }
  .brand {
    position: absolute; left: 32px; top: 232px;
    display: flex; align-items: center; gap: 14px;
  }
  .brand-dot {
    width: 58px; height: 58px; border-radius: 50%;
    background: var(--logo-blue);
  }
  .brand-name {
    font-size: 66px; font-weight: 400; color: var(--logo-blue);
    letter-spacing: 1px; line-height: 1;
  }
  .divider {
    position: absolute; left: 544px; top: 144px;
    width: 3px; height: 236px; background: var(--logo-blue);
  }
  .contact-list {
    position: absolute; left: 585px; top: 196px;
    list-style: none;
  }
  .contact-list li {
    font-size: 30px; color: var(--ink-navy);
    line-height: 1; height: 64px;
  }
  .services-band {
    position: absolute; left: 0; bottom: 0; width: 100%; height: 140px;
    background: linear-gradient(90deg, var(--band-blue), var(--band-blue-deep));
    color: var(--services-light);
  }
  .services-label {
    position: absolute; left: 31px; top: 30px;
    font-size: 32px;
  }
  .service {
    position: absolute; display: flex; align-items: center; gap: 10px;
    font-size: 30px; white-space: nowrap;
  }
  .service svg { width: 26px; height: 26px; }
  .service--oss { left: 205px; top: 28px; }
  .service--consult { left: 577px; top: 28px; }
  .service--web { left: 205px; top: 75px; }
</style>
</head>
<body>
  <main class="business-card">
    <header class="name-band">
      <h1 class="holder-name">Corwin T. Aldous</h1>
    </header>

    <div class="brand">
      <span class="brand-dot" aria-hidden="true"></span>
      <span class="brand-name">KITE LOFT</span>
    </div>

    <div class="divider" aria-hidden="true"></div>

    <ul class="contact-list">
      <li>0431 587 904</li>
      <li>www.kiteloftdev.example</li>
      <li>corwin@kiteloftdev.example</li>
    </ul>

    <footer class="services-band">
      <span class="services-label">Services :</span>
      <span class="service service--oss">
        <svg viewBox="0 0 26 26" aria-hidden="true"><g stroke="currentColor" stroke-width="2" stroke-linecap="round"><line x1="13" y1="3" x2="13" y2="23"/><line x1="4.3" y1="8" x2="21.7" y2="18"/><line x1="4.3" y1="18" x2="21.7" y2="8"/></g><circle cx="13" cy="13" r="3.5" fill="currentColor"/></svg>
        Open Source Software
      </span>
      <span class="service service--consult">
        <svg viewBox="0 0 26 26" aria-hidden="true"><g stroke="currentColor" stroke-width="2" stroke-linecap="round"><line x1="13" y1="3" x2="13" y2="23"/><line x1="4.3" y1="8" x2="21.7" y2="18"/><line x1="4.3" y1="18" x2="21.7" y2="8"/></g><circle cx="13" cy="13" r="3.5" fill="currentColor"/></svg>
        Consulting For Developers
      </span>
      <span class="service service--web">
        <svg viewBox="0 0 26 26" aria-hidden="true"><g stroke="currentColor" stroke-width="2" stroke-linecap="round"><line x1="13" y1="3" x2="13" y2="23"/><line x1="4.3" y1="8" x2="21.7" y2="18"/><line x1="4.3" y1="18" x2="21.7" y2="8"/></g><circle cx="13" cy="13" r="3.5" fill="currentColor"/></svg>
        Web Development For Muggles
      </span>
    </footer>
  </main>
</body>
</html>
```